Thornvale Group needs a business card design

We need a new business card design using the logo recently selected in a logo competition on Pixel Bazaar. Our business is a consultancy specializing in aviation and energy and the winning business card design will promote an image of precision and professionalism with creativity.

Please use the logo with the name on the front of the card and use a complementary font. Make the back white with either the light grey or dark grey logo.

Target Market(s)

Senior finance and legal leaders at aviation and energy companies

Industry/Entity Type

Management Consulting

Contact Information for Business Card

Peter Castrell
President
Thornvale Group

www.thornvalegroup.example

(555) 204-6391
pc@thornvalegroup.example

Requirements
Must have
• Professional font that goes well with the logo font

```html
<!DOCTYPE html>
<html lang="en">
<head>
<meta charset="utf-8">
<title>Thornvale Group – Business Card</title>
<link href="https://fonts.googleapis.com/css2?family=Source+Sans+3:wght@400;600&display=swap" rel="stylesheet">
<style>
  :root {
    --backdrop: #151515;
    --card-white: #ffffff;
    --navy: #15406e;
    --navy-text: #1b3a6a;
    --navy-soft: #2a5486;
    --grey-text: #505050;
  }
  * { margin: 0; padding: 0; box-sizing: border-box; }
  html, body {
    width: 1200px; height: 900px; overflow: hidden;
    background: var(--backdrop);
    font-family: "Source Sans 3", "Segoe UI", sans-serif;
  }
  .canvas { position: relative; width: 1200px; height: 900px; }
  .card {
    position: absolute; top: 170px; width: 347px; height: 561px;
  }
  .card-front { left: 259px; background: var(--card-white); color: var(--grey-text); text-align: center; }
  .card-back { left: 631px; background: var(--navy); }

  .accent-band {
    position: absolute; left: 102px; width: 143px; background: var(--navy);
  }
  .accent-band.top { top: 0; height: 30px; }
  .accent-band.bottom { bottom: 0; height: 28px; }

  .brand-name {
    position: absolute; left: 0; right: 0; top: 190px;
    font-size: 29px; font-weight: 400; letter-spacing: 3px;
    text-transform: uppercase; color: var(--navy-text);
  }
  .holder-name {
    position: absolute; left: 0; right: 0; top: 316px;
    font-size: 18px; font-weight: 600; color: var(--navy-text);
  }
  .holder-title {
    position: absolute; left: 0; right: 0; top: 339px;
    font-size: 15px;
  }
  .contact-line {
    position: absolute; left: 0; right: 0;
    font-size: 15px; display: flex; justify-content: center; align-items: center; gap: 7px;
  }
  .contact-line.phone { top: 376px; }
  .contact-line.email { top: 396px; }
  .contact-line svg { fill: var(--navy-text); }
  .service-line {
    position: absolute; left: 0; right: 0; top: 449px;
    font-size: 17px; font-weight: 600; color: var(--navy-text); letter-spacing: -0.3px;
  }
  .sector-line {
    position: absolute; left: 0; right: 0; top: 476px;
    font-size: 17px; letter-spacing: -0.3px;
  }

  .back-brand {
    position: absolute; left: 0; right: 0; top: 262px; text-align: center;
    font-size: 26px; font-weight: 400; letter-spacing: 3px;
    text-transform: uppercase; color: var(--navy-soft);
  }
</style>
</head>
<body>
<div class="canvas">
  <section class="card card-front">
    <div class="accent-band top"></div>
    <div class="brand-name">Thornvale Group</div>
    <div class="holder-name">Peter J. Castrell</div>
    <div class="holder-title">President</div>
    <div class="contact-line phone">
      <svg width="12" height="12" viewBox="0 0 24 24" aria-hidden="true"><path d="M6.6 10.8a15.1 15.1 0 0 0 6.6 6.6l2.2-2.2a1 1 0 0 1 1-.25 11.4 11.4 0 0 0 3.6.57 1 1 0 0 1 1 1V20a1 1 0 0 1-1 1A17 17 0 0 1 3 4a1 1 0 0 1 1-1h3.5a1 1 0 0 1 1 1c0 1.25.2 2.45.57 3.6a1 1 0 0 1-.25 1z"/></svg>
      <span>(555) 204-6391</span>
    </div>
    <div class="contact-line email">
      <svg width="11" height="9" viewBox="0 0 22 16" aria-hidden="true"><path d="M0 0h22v16H0z M2 2v.6l9 6 9-6V2z" fill-rule="evenodd"/></svg>
      <span>pc@thornvalegroup.example</span>
    </div>
    <div class="service-line">Finance and Strategy Consulting</div>
    <div class="sector-line">Aviation - Manufacturing - Energy</div>
    <div class="accent-band bottom"></div>
  </section>

  <section class="card card-back">
    <div class="back-brand">Thornvale Group</div>
  </section>
</div>
</body>
</html>
```